Cool business cards

Use my existing logo from mark meadow (see images I have uploaded) and design a really cool non-stuffy business card. I am a divorce mediator.

```html
<!DOCTYPE html>
<html lang="en">
<head>
<meta charset="utf-8">
<title>Mark Meadow – Business Card</title>
<link href="https://fonts.googleapis.com/css2?family=Roboto:wght@400;500&family=Saira+Semi+Condensed:wght@600&display=swap" rel="stylesheet">
<style>
  :root {
    --backdrop: #b9b9b9;
    --teal: #2f9ca3;
    --green: #3a8862;
    --brand-green: #2f8a5c;
    --paper: #f4f4f3;
    --ink: #2b2b2b;
    --rule: #a9a9a9;
    --white: #ffffff;
  }
  * { margin: 0; padding: 0; box-sizing: border-box; }
  html, body { width: 1200px; height: 576px; overflow: hidden; }
  body {
    background: var(--backdrop);
    font-family: "Roboto", Arial, sans-serif;
    position: relative;
  }
  .card {
    position: absolute;
    border-radius: 14px;
    overflow: hidden;
  }
  .card-front {
    left: 82px; top: 139px; width: 484px; height: 293px;
    background: linear-gradient(100deg, var(--teal) 0%, #379493 45%, var(--green) 100%);
  }
  .card-back {
    left: 602px; top: 138px; width: 480px; height: 291px;
    background: var(--paper);
  }
  .brand {
    position: absolute;
    display: flex; justify-content: center; align-items: center;
  }
  .brand-name {
    font-family: "Roboto", Arial, sans-serif;
    font-weight: 400;
    white-space: nowrap;
    line-height: 1;
  }
  .card-front .brand { left: 0; right: 0; top: 0; bottom: 0; }
  .card-front .brand-name { color: var(--white); font-size: 44px; }

  .card-back .brand { left: 0; width: 252px; top: 0; bottom: 0; }
  .card-back .brand-name { color: var(--brand-green); font-size: 24px; }

  .divider {
    position: absolute; left: 252px; top: 50px;
    width: 1px; height: 193px; background: var(--rule);
  }
  .contact { position: absolute; left: 280px; top: 66px; color: var(--ink); }
  .person-name {
    font-family: "Saira Semi Condensed", "Arial Narrow", sans-serif;
    font-weight: 600; font-size: 20px; color: var(--brand-green); line-height: 1.1;
  }
  .person-role { font-size: 12.5px; margin-top: 4px; }
  .contact-list { list-style: none; margin-top: 22px; }
  .contact-list li {
    display: flex; align-items: center; gap: 10px;
    font-size: 12.5px; height: 18.5px;
  }
  .contact-icon { width: 12px; height: 12px; flex: none; }
  .address { font-size: 12.5px; line-height: 18.5px; margin-top: 6px; margin-left: 3px; }
</style>
</head>
<body>
  <section class="card card-front" aria-label="Card front">
    <div class="brand">
      <span class="brand-name">Mark Meadow</span>
    </div>
  </section>

  <section class="card card-back" aria-label="Card back">
    <div class="brand">
      <span class="brand-name">Mark Meadow</span>
    </div>
    <div class="divider"></div>
    <div class="contact">
      <div class="person-name">Dana Ellis Hart</div>
      <div class="person-role">Managing Director</div>
      <ul class="contact-list">
        <li>
          <svg class="contact-icon" viewBox="0 0 12 12" aria-hidden="true"><path d="M1 4 Q6 0 11 4 L9 5 L8 3.5 Q6 3 4 3.5 L3 5 Z" fill="#2f8a5c"/><rect x="2.5" y="5.5" width="7" height="5" rx="1" fill="#2f8a5c"/></svg>
          <span>555-014-2230</span>
        </li>
        <li>
          <svg class="contact-icon" viewBox="0 0 12 12" aria-hidden="true"><rect x="0.5" y="2.5" width="11" height="7.5" fill="#2f8a5c"/><path d="M0.5 2.5 L6 7 L11.5 2.5" stroke="#f4f4f3" stroke-width="1" fill="none"/></svg>
          <span>dana@markmeadow.com</span>
        </li>
        <li>
          <svg class="contact-icon" viewBox="0 0 12 12" aria-hidden="true"><circle cx="6" cy="6" r="5" fill="#2f8a5c"/><path d="M1 6 H11 M6 1 V11 M6 1 Q3 6 6 11 M6 1 Q9 6 6 11" stroke="#f4f4f3" stroke-width="0.7" fill="none"/></svg>
          <span>www.markmeadow.com</span>
        </li>
      </ul>
      <p class="address">18 Willow Lane, Fairview,<br>Brookdale, US 40218</p>
    </div>
  </section>
</body>
</html>
```